Business Card Design

New business card design

Target Market(s)

Residential & Commercial Property Managers

Industry/Entity Type

Plumbing Services

Contact Information for Business Card

Name - Rowan Keddle, title - Director, Phone Number - 0431 286 517, email - rowan@tbk-plumbing.com.au, Company ABN - 73 215 904 386,

Font styles to use
Sans Serif

Colors
0054AA
0677BA
7BADD7
CADEEF
E8F1F8

```html
<!DOCTYPE html>
<html lang="en">
<head>
<meta charset="utf-8">
<title>TBK Plumbing Services – Business Card</title>
<link rel="stylesheet" href="https://fonts.googleapis.com/css2?family=Poppins:wght@300;400;500;600&display=swap">
<style>
  :root {
    --backdrop: #222222;
    --card: #1c232a;
    --card-edge: #161b21;
    --blue: #2aa6e0;
    --white: #f2f4f6;
    --taupe: #8a7d70;
    --muted: #8b949c;
    --emboss: #12171c;
  }
  * { margin: 0; padding: 0; box-sizing: border-box; }
  html, body { width: 1200px; height: 780px; overflow: hidden; background: var(--backdrop); }
  body { font-family: "Poppins", sans-serif; position: relative; }

  .card {
    position: absolute;
    top: 235px;
    width: 540px;
    height: 309px;
    background: var(--card);
    border-radius: 3px;
    box-shadow: 0 18px 40px rgba(0,0,0,.55);
    overflow: hidden;
  }
  .card--front { left: 40px; }
  .card--back { left: 620px; }

  .front-band {
    position: absolute;
    left: -40px; top: 150px;
    width: 620px; height: 90px;
    background: linear-gradient(180deg, rgba(0,0,0,0) 0%, rgba(0,0,0,.22) 55%, rgba(0,0,0,0) 100%);
    transform: rotate(-4deg);
  }

  .brand { position: absolute; left: 60px; top: 48px; display: flex; align-items: center; gap: 10px; }
  .brand__name { font-weight: 400; font-size: 52px; line-height: 1; color: var(--white); letter-spacing: 1px; }
  .brand__dot { width: 14px; height: 14px; border-radius: 50%; background: var(--blue); margin-top: 28px; }
  .brand__tag { position: absolute; left: 64px; top: 112px; font-size: 9px; font-weight: 400; letter-spacing: 7px; color: var(--white); }

  .person { position: absolute; left: 150px; top: 140px; }
  .person__name { font-size: 26px; line-height: 1; font-weight: 300; color: var(--taupe); }
  .person__first { font-weight: 600; color: var(--blue); }
  .person__title { font-size: 12px; font-weight: 500; color: var(--white); margin: 4px 0 0 86px; }
  .person__abn { font-size: 12px; color: var(--blue); margin-top: 10px; letter-spacing: .5px; }

  .contacts { position: absolute; left: 150px; top: 226px; display: grid; grid-template-columns: 18px auto; column-gap: 10px; row-gap: 5px; align-items: center; }
  .contacts__icon { width: 16px; height: 14px; border-radius: 3px; background: var(--blue); display: flex; align-items: center; justify-content: center; }
  .contacts__text { font-size: 11px; color: var(--white); letter-spacing: .3px; }

  .back-brand { position: absolute; left: 0; right: 0; top: 92px; text-align: center; }
  .back-brand__row { display: inline-flex; align-items: center; gap: 14px; }
  .back-brand__name { font-weight: 400; font-size: 96px; line-height: 1; color: var(--emboss); letter-spacing: 2px; }
  .back-brand__dot { width: 26px; height: 26px; border-radius: 50%; background: var(--blue); margin-top: 50px; }
  .back-brand__tag { display: block; margin-top: 10px; font-size: 13px; letter-spacing: 12px; color: var(--emboss); }
</style>
</head>
<body>
  <section class="card card--front" aria-label="Business card front">
    <div class="front-band"></div>
    <div class="brand">
      <span class="brand__name">tbk</span>
      <span class="brand__dot"></span>
    </div>
    <span class="brand__tag">plumbing services</span>

    <div class="person">
      <p class="person__name"><span class="person__first">Rowan</span> Keddle</p>
      <p class="person__title">Director</p>
      <p class="person__abn">ABN - 73 215 904 386</p>
    </div>

    <div class="contacts">
      <span class="contacts__icon">
        <svg width="10" height="8" viewBox="0 0 10 8"><path d="M1 3 Q5 -1 9 3 L7.5 4.5 L6.5 3.5 Q5 3 3.5 3.5 L2.5 4.5 Z M2.5 6 H7.5 V7.5 H2.5 Z" fill="#fff"/></svg>
      </span>
      <span class="contacts__text">0431 286 517</span>
      <span class="contacts__icon">
        <svg width="10" height="8" viewBox="0 0 10 8"><path d="M1 3 L3 1 H7 L9 3 L5 7.5 Z" fill="none" stroke="#fff" stroke-width="1"/></svg>
      </span>
      <span class="contacts__text">www.tbk-plumbing.com.au</span>
      <span class="contacts__icon">
        <svg width="10" height="10" viewBox="0 0 10 10"><circle cx="5" cy="5" r="4" fill="none" stroke="#fff" stroke-width="1"/><path d="M1 5 H9 M5 1 Q2.5 5 5 9 M5 1 Q7.5 5 5 9" fill="none" stroke="#fff" stroke-width=".8"/></svg>
      </span>
      <span class="contacts__text">rowan@tbk-plumbing.com.au</span>
    </div>
  </section>

  <section class="card card--back" aria-label="Business card back">
    <div class="back-brand">
      <span class="back-brand__row">
        <span class="back-brand__name">tbk</span>
        <span class="back-brand__dot"></span>
      </span>
      <span class="back-brand__tag">plumbing services</span>
    </div>
  </section>
</body>
</html>
```